Business Card for a Jewellery Brand

Business card for an upscale jewellery brand. Attached is the brand logo and icon and color board. I am looking for two card versions: one for the founder and one is generic. The card should be elegant and convey upscale and premium feel. I am open to both square and rectangle card shapes.

Industry/Entity Type

Jewelry

Contact Information for Business Card

Two cards: (1) Sunela Parvaniya (Founder) (2) General
(1) Sunela Parvaniya card should have Name: Sunela Parvaniya, Title: Founder Email id: sunela@quiremo.com.au. Phone no: +61452913307
(2) Generic card should have Email id: info@quiremo.com.au. Phone no: +61436207518

Requirements
Must have
• Workmark
• ICON
• Phone no
• Email ID
• ABN: 58219740312 (Note: ABN is Business number in Australia)
• Website: www.quiremo.com.au
• Instagram: quiremo_jewellery
• Facebook: @quiremojewellery
Nice to have
• Tagline

```html
<!DOCTYPE html>
<html lang="en">
<head>
<meta charset="utf-8">
<title>Quiremo Business Cards</title>
<link href="https://fonts.googleapis.com/css2?family=Open+Sans:wght@300;400;600;700&display=swap" rel="stylesheet">
<style>
  :root {
    --backdrop: #3b3633;
    --card: #141414;
    --rose: #d9958f;
    --ink: #f1f1f1;
    --muted: #bdbdbd;
  }
  * { box-sizing: border-box; margin: 0; padding: 0; }
  html, body {
    width: 1200px; height: 864px; overflow: hidden;
    background: var(--backdrop);
    font-family: "Open Sans", Arial, sans-serif;
  }
  .stage {
    width: 1200px; height: 864px;
    display: flex; align-items: center; justify-content: center; gap: 40px;
  }
  .card {
    width: 520px; height: 297px;
    background: var(--card);
    position: relative;
    box-shadow: 0 12px 30px rgba(0,0,0,.45);
  }
  /* Back side */
  .card-back .wordmark {
    position: absolute; left: 0; right: 0; top: 100px;
    text-align: center;
    color: var(--rose);
    font-weight: 300; font-size: 42px; letter-spacing: 14px;
    padding-left: 14px;
  }
  .card-back .tagline-rule {
    position: absolute; left: 60px; right: 60px; top: 205px;
    height: 1px;
    background: linear-gradient(90deg, rgba(240,240,240,.1), rgba(240,240,240,.75) 40%, rgba(240,240,240,.1));
  }
  .card-back .tagline {
    position: absolute; left: 92px; top: 213px;
    color: var(--muted);
    font-size: 10px; letter-spacing: 2px;
  }
  /* Front side */
  .card-front .brand {
    position: absolute; left: 0; top: 0; width: 265px; height: 100%;
    display: flex; align-items: center; justify-content: center;
  }
  .card-front .wordmark {
    color: var(--rose);
    font-weight: 400; font-size: 36px; letter-spacing: 9px;
    padding-left: 9px;
  }
  .card-front .divider {
    position: absolute; left: 275px; top: 45px; bottom: 45px; width: 1px;
    background: linear-gradient(180deg, rgba(240,240,240,0), rgba(240,240,240,.85) 50%, rgba(240,240,240,0));
  }
  .card-front .details {
    position: absolute; left: 295px; top: 60px;
    color: var(--ink);
  }
  .person-name { color: var(--rose); font-weight: 700; font-size: 15px; line-height: 1.3; }
  .person-role { font-size: 14px; line-height: 1.3; }
  .abn { font-size: 13px; margin-top: 4px; margin-bottom: 6px; }
  .contact-list { list-style: none; }
  .contact-list li {
    display: flex; align-items: center; gap: 9px;
    font-size: 13px; line-height: 21px;
  }
  .contact-list svg { width: 11px; height: 11px; flex: none; }
  .icon { fill: var(--rose); }
  .icon-line { fill: none; stroke: var(--rose); stroke-width: 1.5; }
</style>
</head>
<body>
<main class="stage">
  <section class="card card-back" aria-label="Card back">
    <div class="wordmark">QUIREMO</div>
    <div class="tagline-rule"></div>
    <div class="tagline">LOVE IS IN THE AIR</div>
  </section>

  <section class="card card-front" aria-label="Card front">
    <div class="brand"><div class="wordmark">QUIREMO</div></div>
    <div class="divider"></div>
    <div class="details">
      <div class="person-name">Sunela Parvaniya</div>
      <div class="person-role">Founder</div>
      <div class="abn">ABN: 58219740312</div>
      <ul class="contact-list">
        <li><svg viewBox="0 0 12 12" aria-hidden="true"><rect class="icon-line" x="3" y="0.8" width="6" height="10.4" rx="1"/><rect class="icon" x="5" y="9" width="2" height="1"/></svg>+61452913307</li>
        <li><svg viewBox="0 0 12 12" aria-hidden="true"><rect class="icon-line" x="0.8" y="2.3" width="10.4" height="7.4"/><path class="icon-line" d="M0.8 2.5 L6 6.8 L11.2 2.5"/></svg>sunela@quiremo.com.au</li>
        <li><svg viewBox="0 0 12 12" aria-hidden="true"><path class="icon" d="M6 0.5a4 4 0 0 1 4 4c0 3-4 7-4 7s-4-4-4-7a4 4 0 0 1 4-4z"/><circle cx="6" cy="4.5" r="1.5" fill="#141414"/></svg>www.quiremo.com.au</li>
        <li><svg viewBox="0 0 12 12" aria-hidden="true"><rect class="icon" x="1" y="1" width="10" height="10" rx="1.5"/></svg>quiremo_jewellery</li>
        <li><svg viewBox="0 0 12 12" aria-hidden="true"><rect class="icon" x="1" y="1" width="10" height="10" rx="1.5"/></svg>@quiremojewellery</li>
      </ul>
    </div>
  </section>
</main>
</body>
</html>
```